NEW Modern Sleek Business Card for VR Language Startup

Our startup is using VR to lead the next wave of world language education. We need a two-sided business card that introduces the larger organization (Brightloom Language Inc) and our contact info on one side and shows the product, Glimwoorld, on the other side.

Side 1 (contact info)= Brightloom Logo and Contact info (name, title, phone, email)

Side 2 (product)= Glimworld logo, text, and website
Text= Culturally Immersive Language Learning Games
Website= www.glimworld-play.com

Target Market(s)

Education, Technology

Contact Information for Business Card

Contact info will be updated upon approval of the design. For now, put this as a placeholder.

Perry Dunmore
Founder & CEO
pdunmore@quillpost-mail.net
(555)-014-2286

Font styles to use
Other font styles liked:
• Gibson and Century Gothic are the brand fonts

Requirements
Nice to have
• I would love to see cohesion between the design and colors of the two logos. I have attached a few business card designs that I like, so you can get a feel for my preferred style.

```html
<!DOCTYPE html>
<html lang="en">
<head>
<meta charset="utf-8">
<title>Brightloom Language – Business Card</title>
<link href="https://fonts.googleapis.com/css2?family=Lato:wght@400;700&family=Montserrat:wght@600&display=swap" rel="stylesheet">
<style>
  :root {
    --backdrop: #e9e6e2;
    --card-white: #ffffff;
    --ink: #1f1f1f;
    --charcoal: #1e1e1e;
    --slate: #555555;
    --orange: #f2703a;
    --amber: #f6a33a;
    --violet: #7a55e0;
    --indigo: #5b5cf0;
    --sky: #3aa4f0;
    --cyan: #38c4e8;
    --coral: #f08a5a;
    --light-text: #ffffff;
  }
  * { box-sizing: border-box; margin: 0; padding: 0; }
  html, body { width: 1200px; height: 900px; overflow: hidden; }
  body {
    position: relative;
    background: var(--backdrop);
    font-family: "Lato", Arial, sans-serif;
  }
  .card {
    position: absolute;
    width: 556px;
    height: 343px;
    background: var(--card-white);
    overflow: hidden;
    box-shadow: 0 3px 8px rgba(0,0,0,0.25);
  }
  .card--contact { left: 330px; top: 90px; }
  .card--product { left: 330px; top: 469px; width: 559px; }
  .card__wave { position: absolute; inset: 0; width: 100%; height: 100%; }

  .brand-mark {
    position: absolute;
    display: flex;
    flex-direction: column;
    align-items: flex-start;
    gap: 12px;
  }
  .brand-mark__dot { border-radius: 50%; }
  .brand-mark__name { font-family: "Montserrat", "Century Gothic", sans-serif; font-weight: 600; white-space: nowrap; }

  .card--contact .brand-mark { left: 36px; top: 56px; }
  .card--contact .brand-mark__dot { width: 76px; height: 76px; margin-left: 50px; background: var(--orange); }
  .card--contact .brand-mark__name { font-size: 22px; color: var(--ink); letter-spacing: 0.5px; }

  .card--product .brand-mark { left: 40px; top: 42px; }
  .card--product .brand-mark__dot { width: 104px; height: 104px; margin-left: 36px; background: var(--sky); }
  .card--product .brand-mark__name { font-size: 34px; line-height: 40px; color: var(--indigo); }

  .contact {
    position: absolute;
    right: 32px;
    top: 200px;
    text-align: right;
    color: var(--light-text);
  }
  .contact__name {
    font-size: 21px;
    font-weight: 400;
    letter-spacing: 0.5px;
    background: linear-gradient(90deg, var(--coral), var(--violet));
    -webkit-background-clip: text;
    background-clip: text;
    color: transparent;
    line-height: 26px;
  }
  .contact__title { font-size: 15px; line-height: 20px; }
  .contact__list { list-style: none; margin-top: 20px; font-size: 15px; line-height: 22px; }
  .contact__item { display: flex; justify-content: flex-end; align-items: center; gap: 6px; }
  .contact__icon { width: 13px; height: 11px; }

  .product-info {
    position: absolute;
    right: 34px;
    top: 229px;
    text-align: right;
    color: var(--light-text);
  }
  .product-info__tagline { font-size: 16px; line-height: 20px; text-transform: uppercase; letter-spacing: 0.3px; }
  .product-info__site { margin-top: 20px; font-size: 17px; color: var(--cyan); letter-spacing: 1.2px; }
</style>
</head>
<body>

<section class="card card--contact" aria-label="Contact side">
  <svg class="card__wave" viewBox="0 0 556 343" preserveAspectRatio="none" aria-hidden="true">
    <defs>
      <linearGradient id="warm-stripe" x1="0" x2="1">
        <stop offset="0" stop-color="#f2703a"/>
        <stop offset="0.65" stop-color="#f2703a"/>
        <stop offset="1" stop-color="#f6a33a"/>
      </linearGradient>
    </defs>
    <path d="M0,258 C170,258 300,128 452,128 C300,138 180,272 0,272 Z" fill="url(#warm-stripe)"/>
    <path d="M0,272 C190,272 310,136 450,136 C505,136 540,148 556,160 L556,172 C536,158 505,146 452,146 C315,146 195,278 0,278 Z" fill="var(--violet)"/>
    <path d="M0,281 C195,281 318,150 462,150 C320,156 200,287 0,287 Z" fill="var(--sky)"/>
    <path d="M0,294 C190,294 318,160 458,160 C512,160 540,170 556,182 L556,343 L0,343 Z" fill="var(--charcoal)"/>
  </svg>

  <div class="brand-mark">
    <span class="brand-mark__dot" aria-hidden="true"></span>
    <span class="brand-mark__name">Brightloom Language</span>
  </div>

  <div class="contact">
    <h1 class="contact__name">PERRY DUNMORE</h1>
    <p class="contact__title">Founder &amp; CEO</p>
    <ul class="contact__list">
      <li class="contact__item">(555)-014-2286
        <svg class="contact__icon" viewBox="0 0 13 11" aria-hidden="true"><path d="M1,3 Q6.5,-1 12,3 L10,5 L8,3.5 L5,3.5 L3,5 Z M3,6 L10,6 L12,10 L1,10 Z" fill="var(--coral)"/></svg>
      </li>
      <li class="contact__item">pdunmore@quillpost-mail.net
        <svg class="contact__icon" viewBox="0 0 13 11" aria-hidden="true"><rect x="0.5" y="1" width="12" height="9" fill="var(--violet)"/><path d="M0.5,1 L6.5,6 L12.5,1" fill="none" stroke="#fff" stroke-width="1"/></svg>
      </li>
    </ul>
  </div>
</section>

<section class="card card--product" aria-label="Product side">
  <svg class="card__wave" viewBox="0 0 559 343" preserveAspectRatio="none" aria-hidden="true">
    <path d="M0,260 C190,260 305,130 458,130 C305,140 195,274 0,274 Z" fill="var(--indigo)"/>
    <path d="M0,276 C195,276 310,138 450,138 C510,138 542,150 559,160 L559,172 C540,162 508,152 455,152 C318,152 200,283 0,283 Z" fill="var(--sky)"/>
    <path d="M0,290 C198,290 320,162 460,162 C515,162 542,170 559,182 L559,343 L0,343 Z" fill="var(--slate)"/>
  </svg>

  <div class="brand-mark">
    <span class="brand-mark__dot" aria-hidden="true"></span>
    <span class="brand-mark__name">Glimworld</span>
  </div>

  <div class="product-info">
    <p class="product-info__tagline">Culturally Immersive<br>Language Learning Games</p>
    <p class="product-info__site">www.glimworld-play.com</p>
  </div>
</section>

</body>
</html>
```